Looking for a cool, modern Cannabis Jar Label

I want you to come up with a better, modern look for a label.

I need it sized to 4” x 3” - I plan to print directly to label printer.

I want you to use Photoshop and deliver me a layered PSD file that I can edit and modify the information as needed..

The label information will need to include places for:
(1) Strain Name - most important part of label - larger font size than rest - example Kestrel Mist, PLV #7, Juniper Hollow
(2) Pricing - for Gram, 1/8, 1/4, 1/2. and Ounce
(3) Strain Designation (Hybrid, Indica or Sativa) - maybe color coded, different color for Indica v. Sativa, just an idea
(4) THC and CBD percentages - for example 23% THC and 0.05% CBD
(5) Farm name - a place where we can add the name/logo of the business that produced the product. example - Ovenrow Farms

I have attached a simple mockup showing the information.

I have also attached a few samples of labels we like to give you an idea of the look and feel we are going for.

I am wanting a very clean, modern, classy, readable look.The font will use is Gotham Font.

HI Everyone! Thank you for all of your designs. I am requesting an extension because I need more time to give adequate feedback to the designers. Thank you for your participation and all of your efforts! I will be making a decision soon!

• Gotham Font

• Thank you for your designs. I am sorry i have been slow in providing feedback, things have been really busy around here!
• I wanted to give some group general feedback. After reviewing all of the designs, there is a common theme among all of the designs that I would like to see changed.
• I would like to see the per gram pricing more prominent on the label. This is what most people are looking for when they are purchasing the product. So I would like to see this stand out from the other pricing tiers. As I think about it, they don't all need to be grouped together in a line. You could have the Per Gram pricing front and center some where and then the other pricing tiers grouped together somewhere else on the label.
• This is the order of importance of items on the label. Items at the the top of the list should be bigger than those below it.
• 1. Strain name
• 2. Pricing - being per gram the most important of all prices
• 3. THC/CBD percentages
• 4. Strain Type (indica, sativa, hybrid)
• 5. Farm name/logo
• When laying out these labels, they will be going on rounded jars and they will be on display. Think of jars with fancy labels in a candy store. They need to be eye catchy, appealing, but easy read.
• Thank you for all of your hard work, everyone is doing a great job.
• Best,
• Neta

```html
<!DOCTYPE html>
<html lang="en">
<head>
<meta charset="utf-8">
<title>Kestrel Mist — Jar Label</title>
<link href="https://fonts.googleapis.com/css2?family=Montserrat:wght@300;400;600;800&display=swap" rel="stylesheet">
<style>
  :root{
    --maroon:#880606;
    --brick:#9e3a3a;
    --coral:#cd5555;
    --blush:#e0c4c4;
    --rule:#dcbcbc;
    --ink:#111111;
    --paper:#ffffff;
  }
  html,body{margin:0;padding:0;width:1200px;height:917px;overflow:hidden;background:var(--paper);}
  body{font-family:"Montserrat",sans-serif;position:relative;}
  .label{position:absolute;left:33px;top:33px;width:1126px;height:845px;background:var(--maroon);}
  .abs{position:absolute;}

  .strain{left:42px;top:18px;color:var(--paper);font-weight:400;line-height:1;white-space:nowrap;}
  .strain-name{font-size:108px;letter-spacing:1px;}
  .strain-sub{font-size:82px;margin-top:10px;letter-spacing:1px;}

  .code-number{left:966px;top:6px;width:152px;height:177px;background:var(--brick);color:var(--paper);}
  .code-number .hash{position:absolute;left:14px;top:138px;font-size:34px;font-weight:400;line-height:1;}
  .code-number .digit{position:absolute;left:30px;top:4px;width:122px;text-align:center;font-size:176px;font-weight:300;line-height:1;}
  .code-letters{left:966px;top:185px;width:152px;height:71px;background:var(--coral);color:var(--paper);
    font-size:52px;font-weight:400;text-align:center;line-height:76px;letter-spacing:1px;}

  .prices{left:6px;top:256px;width:1112px;height:337px;background:var(--paper);}
  .tier{position:absolute;top:60px;height:119px;border-right:4px solid var(--rule);border-bottom:4px solid var(--rule);box-sizing:border-box;}
  .tier .unit{position:absolute;right:10px;top:-6px;font-size:28px;font-weight:300;color:var(--ink);}
  .tier .amount{position:absolute;left:4px;bottom:4px;font-size:64px;font-weight:300;color:var(--ink);line-height:1;}
  .strain-type{position:absolute;left:0;width:100%;top:218px;text-align:center;font-size:92px;font-weight:300;color:var(--maroon);line-height:1;}

  .potency{left:6px;top:600px;width:764px;height:239px;}
  .potency svg{position:absolute;left:0;top:0;}
  .reading{position:absolute;text-align:left;line-height:1;}
  .reading .value{font-size:116px;font-weight:300;letter-spacing:-2px;}
  .reading .pct{font-size:50px;font-weight:400;vertical-align:top;position:relative;top:4px;}
  .reading .cannabinoid{font-size:62px;font-weight:300;margin-top:8px;}
  .thc{left:92px;top:40px;color:var(--paper);}
  .thc .cannabinoid{margin-left:10px;}
  .cbd{left:418px;top:40px;color:var(--ink);}
  .cbd .cannabinoid{margin-left:80px;}

  .grower-tag{left:778px;top:600px;width:340px;height:56px;background:var(--coral);color:var(--paper);
    font-size:40px;font-weight:300;text-align:center;line-height:56px;letter-spacing:1px;}
  .grower{left:778px;top:656px;width:340px;height:183px;background:var(--paper);display:flex;align-items:center;justify-content:center;gap:18px;}
  .grower .mark{width:66px;height:66px;border-radius:50%;background:var(--ink);flex:none;}
  .grower .farm-name{font-size:34px;font-weight:800;color:var(--ink);line-height:1.05;}
</style>
</head>
<body>
<div class="label">
  <div class="abs strain">
    <div class="strain-name">Kestrel Mist</div>
    <div class="strain-sub">Juniper Hollow</div>
  </div>

  <div class="abs code-number"><span class="hash">#</span><span class="digit">7</span></div>
  <div class="abs code-letters">PLV</div>

  <div class="abs prices">
    <div class="tier" style="left:17px;width:190px;"><span class="unit">g.</span><span class="amount">$10</span></div>
    <div class="tier" style="left:242px;width:190px;"><span class="unit">1/8</span><span class="amount">$35</span></div>
    <div class="tier" style="left:467px;width:188px;"><span class="unit">1/4</span><span class="amount">$70</span></div>
    <div class="tier" style="left:688px;width:187px;"><span class="unit">1/2</span><span class="amount">$140</span></div>
    <div class="tier" style="left:908px;width:189px;"><span class="unit">Oz</span><span class="amount">$280</span></div>
    <div class="strain-type">Hybrid</div>
  </div>

  <div class="abs potency">
    <svg width="764" height="239" viewBox="0 0 764 239" aria-hidden="true">
      <rect x="0" y="0" width="764" height="239" fill="var(--blush)"/>
      <polygon points="0,0 298,0 434,239 0,239" fill="var(--brick)"/>
    </svg>
    <div class="reading thc"><div class="value">28<span class="pct">%</span></div><div class="cannabinoid">THC</div></div>
    <div class="reading cbd"><div class="value">0.05<span class="pct">%</span></div><div class="cannabinoid">CBD</div></div>
  </div>

  <div class="abs grower-tag">Grown by</div>
  <div class="abs grower">
    <span class="mark"></span>
    <span class="farm-name">OVENROW<br>FARMS</span>
  </div>
</div>
</body>
</html>
```